Breakfast Cafe - The Sunny Nook

It is for my breakfast and lunch cafe with a hawaiian / beach theme. I am open 7 days a week from 7am to 2pm. We serve traditional American food such as omelettes, pancakes, burgers and sandwiches. I'll upload my old card and my new logo to be used. We have a lot of day to day regulars who eat there during the week, our t-shirts actually say 'Locals Only' on them. Hope this helps. Thanks.

Target Market(s)

anyone who has an appetite!

Industry/Entity Type

American Restaurant

Contact Information for Business Card

4815C Marlow Grove Avenue
Long Beach, California
(555) 731-2294

Requirements
Must have
• Address and phone number easily readable.
Nice to have
• beach or tropical theme

```html
<!DOCTYPE html>
<html lang="en">
<head>
<meta charset="utf-8">
<title>The Sunny Nook – Business Card</title>
<link rel="stylesheet" href="https://fonts.googleapis.com/css2?family=Roboto:ital,wght@0,400;0,500;0,700;1,400;1,500&display=swap">
<style>
  :root {
    --backdrop: #8c8c8c;
    --ink-brown: #7a3a12;
    --rust: #b0581c;
    --sea-blue: #4bb6cf;
    --sunset-orange: #f0a030;
    --card-black: #000000;
    --sky-top: #2f74c8;
    --sky-low: #a8cdea;
    --sea: #2b8c9c;
    --sand-light: #f2dc9e;
    --sand-warm: #e8c878;
  }
  * { margin: 0; padding: 0; box-sizing: border-box; }
  html, body {
    width: 1000px;
    height: 1200px;
    overflow: hidden;
    background: var(--backdrop);
    font-family: "Roboto", Arial, sans-serif;
  }
  .card {
    position: absolute;
    left: 214px;
    width: 578px;
    height: 356px;
    overflow: hidden;
    box-shadow: 3px 4px 8px rgba(0,0,0,0.35);
    text-align: center;
  }
  .card-front {
    top: 219px;
    border-radius: 0 48px 0 48px;
  }
  .card-back {
    top: 607px;
    border-radius: 48px 0 48px 0;
    background: var(--card-black);
  }
  .beach-photo {
    position: absolute;
    inset: 0;
    background: linear-gradient(180deg,
      var(--sky-top) 0%,
      var(--sky-low) 28%,
      var(--sea) 34%,
      #7fc4c4 50%,
      var(--sand-light) 58%,
      var(--sand-warm) 100%);
  }
  .front-content {
    position: absolute;
    inset: 0;
    color: var(--ink-brown);
  }
  .line {
    position: absolute;
    left: 0;
    right: 0;
    white-space: nowrap;
  }
  .brand-name {
    font-weight: 700;
    color: var(--sea-blue);
  }
  .card-front .brand-name {
    top: 110px;
    font-size: 46px;
    line-height: 52px;
  }
  .location-line {
    font-weight: 700;
    color: var(--rust);
  }
  .card-front .location-line {
    top: 179px;
    font-size: 15px;
    line-height: 18px;
    letter-spacing: 4px;
  }
  .tagline {
    top: 236px;
    font-size: 19px;
    line-height: 24px;
    font-style: italic;
  }
  .phone {
    top: 265px;
    font-size: 22px;
    line-height: 26px;
    font-style: italic;
    font-weight: 500;
  }
  .hours {
    top: 310px;
    font-size: 20px;
    line-height: 24px;
    font-weight: 500;
  }
  .brand-disc {
    position: absolute;
    left: 214px;
    top: 48px;
    width: 150px;
    height: 150px;
    border-radius: 50%;
    background: var(--sunset-orange);
  }
  .card-back .brand-name {
    top: 202px;
    font-size: 28px;
    line-height: 34px;
  }
  .card-back .location-line {
    top: 245px;
    font-size: 10px;
    line-height: 12px;
    letter-spacing: 3px;
  }
  .address {
    top: 270px;
    font-size: 17px;
    line-height: 21px;
    font-style: normal;
    color: var(--sunset-orange);
  }
</style>
</head>
<body>
  <section class="card card-front">
    <div class="beach-photo" role="img" aria-label="Photo of a sunny tropical beach with ocean waves, golden sand and palm trees"></div>
    <div class="front-content">
      <h1 class="line brand-name">The Sunny Nook</h1>
      <p class="line location-line">LONG BEACH, CA</p>
      <p class="line tagline">Family owned and operated!</p>
      <p class="line phone">P : (555) 731-2294</p>
      <p class="line hours">Breakfast &amp; Lunch 7am - 2pm Daily</p>
    </div>
  </section>

  <section class="card card-back">
    <div class="brand-disc"></div>
    <h2 class="line brand-name">The Sunny Nook</h2>
    <p class="line location-line">LONG BEACH, CA</p>
    <address class="line address">
      4815C Marlow Grove Avenue<br>
      Long Beach, California
    </address>
  </section>
</body>
</html>
```